Business card design for Brivo Engineering Tandem

We need a new business card design along with all the necessary to place an order. The company is Brivo Engineering Tandem and we recently updated our logo.

```html
<!DOCTYPE html>
<html lang="en">
<head>
<meta charset="utf-8">
<title>Brivo Engineering Tandem — Business Card</title>
<link href="https://fonts.googleapis.com/css2?family=Poppins:wght@400;500;600;700&display=swap" rel="stylesheet">
<style>
  :root {
    --backdrop: #3b3b3b;
    --card-dark: #2d2d2d;
    --card-light: #ffffff;
    --brand-yellow: #e2bb1f;
    --brand-grey: #8f8f8f;
    --text-dark: #2a2a2a;
  }
  * { margin: 0; padding: 0; box-sizing: border-box; }
  html, body {
    width: 1200px; height: 689px; overflow: hidden;
    background: var(--backdrop);
    font-family: "Poppins", sans-serif;
  }
  .stage {
    position: relative; width: 1200px; height: 689px;
    display: flex; align-items: center; justify-content: center; gap: 50px;
  }
  .card {
    position: relative; width: 520px; height: 300px;
    border-radius: 22px; overflow: hidden;
  }
  .card--front { background: var(--card-dark); }
  .card--back { background: var(--card-light); }

  .wordmark {
    position: absolute; display: flex; align-items: center; gap: 12px;
    color: var(--brand-grey); font-weight: 600; line-height: 1.05;
  }
  .wordmark__square {
    width: 20px; height: 20px; background: var(--brand-grey); flex: none;
  }
  .card--front .wordmark { left: 60px; top: 112px; font-size: 34px; }
  .card--back .wordmark { left: 40px; top: 88px; font-size: 28px; }

  .card__accent-bar {
    position: absolute; right: 0; top: 34px; width: 10px; height: 36px;
    background: var(--brand-yellow);
  }
  .person { position: absolute; right: 30px; top: 36px; text-align: right; }
  .person__name {
    color: var(--brand-yellow); font-weight: 600; font-size: 21px;
    letter-spacing: 0.5px; text-transform: uppercase;
  }
  .person__title {
    color: var(--text-dark); font-size: 12px; letter-spacing: 1.5px;
    text-transform: uppercase; margin-top: 2px;
  }

  .contact { position: absolute; left: 40px; top: 176px; color: var(--text-dark); font-size: 13px; line-height: 1.35; }
  .contact__row { display: flex; align-items: center; gap: 8px; }
  .contact__icon { width: 12px; height: 12px; flex: none; }
  .contact__address { margin-top: 8px; padding-left: 20px; }

  .card__footer { position: absolute; left: 0; bottom: 0; width: 520px; height: 120px; }
</style>
</head>
<body>
<main class="stage">
  <section class="card card--front" aria-label="Card front">
    <div class="wordmark">
      <span class="wordmark__square"></span>
      <span>Brivo Engineering<br>Tandem</span>
    </div>
  </section>

  <section class="card card--back" aria-label="Card back">
    <span class="card__accent-bar"></span>
    <div class="person">
      <p class="person__name">Dariel Fenwick</p>
      <p class="person__title">Managing Director</p>
    </div>

    <div class="wordmark">
      <span class="wordmark__square"></span>
      <span>Brivo Engineering<br>Tandem</span>
    </div>

    <div class="contact">
      <p class="contact__row">
        <svg class="contact__icon" viewBox="0 0 12 12"><path d="M2.5 1l2 2.3-1 1.2a6.5 6.5 0 0 0 4 4l1.2-1 2.3 2-1.3 1.5C5.5 11 1 6.5 1 2.3z" fill="var(--brand-yellow)"/></svg>
        044-987 654 321
      </p>
      <p class="contact__row">
        <svg class="contact__icon" viewBox="0 0 12 12"><rect x="0.5" y="2" width="11" height="8" fill="var(--brand-yellow)"/><path d="M0.5 2l5.5 4.5L11.5 2" stroke="#fff" fill="none"/></svg>
        hello@brivotandem.com
      </p>
      <p class="contact__row">
        <svg class="contact__icon" viewBox="0 0 12 12"><circle cx="6" cy="6" r="5" fill="none" stroke="var(--brand-yellow)" stroke-width="1.3"/><path d="M1 6h10M6 1c-2.5 3-2.5 7 0 10M6 1c2.5 3 2.5 7 0 10" stroke="var(--brand-yellow)" fill="none"/></svg>
        www.brivotandem.com
      </p>
      <p class="contact__address">123, 7th street<br>Country name, 123456</p>
    </div>

    <svg class="card__footer" viewBox="0 0 520 120" aria-hidden="true">
      <rect x="0" y="113" width="340" height="7" fill="var(--brand-yellow)"/>
      <path d="M340 120V70q0-26 26-26h154v76z" fill="var(--brand-grey)"/>
    </svg>
  </section>
</main>
</body>
</html>
```